New energy tablet requires a logo / packaging design

We need a logo designed for a new energy tablet (capsule) called "Q-Vibe". We would like to see designs that communicate a fun, youthful brand aimed primarily at a demographic of 18 - 35.

This will be a herbal energy tablet to be sold online to to people looking to increase energy and mood lifts.

We do have a previous design that we used before and would like that one to be used again but just revamped a little to give it a fresher look and more depth to the design if possible.

Completely new designs are also welcome if you would prefer but ideally we want it to look as similar to the original one as possible.

We are committed to payment on this design.

Thank you all in advance for your design submissions.

These are to be printed onto black foil zip seal bags to contain 1 pellet only.

Target Market(s)

customers that visit online and high street shops that sell herbal energy products

Industry/Entity Type

Online

Requirements
Must have
• Must have the words Q-VIBE and PELLET in the logo design

```html
<!DOCTYPE html>
<html lang="en">
<head>
<meta charset="utf-8">
<title>Q-Vibe Pellet – Energy Tablet Label</title>
<link rel="stylesheet" href="https://fonts.googleapis.com/css2?family=Oswald:wght@400&family=Roboto+Condensed:wght@700&display=swap">
<style>
  :root {
    --page-bg: #ececec;
    --teal-deep: #062a2a;
    --teal-mid: #0f4b4b;
    --teal-glow: #1b6464;
    --aqua: #74d6d6;
    --aqua-band: #1f7a72;
    --metal-light: #d9d9d9;
    --metal-mid: #9a9a9a;
    --metal-dark: #5e5e5e;
    --white: #ffffff;
  }
  html, body {
    margin: 0;
    width: 1200px;
    height: 1000px;
    overflow: hidden;
    background: var(--page-bg);
  }
  .label {
    position: absolute;
    left: 320px;
    top: 202px;
    width: 560px;
    height: 595px;
    background: linear-gradient(90deg, var(--metal-mid), var(--metal-light) 20%, var(--metal-mid) 50%, var(--metal-light) 80%, var(--metal-dark));
  }
  .label-panel {
    position: absolute;
    left: 20px;
    right: 20px;
    top: 0;
    bottom: 22px;
    background:
      radial-gradient(ellipse 70% 45% at 55% 45%, var(--teal-glow), transparent 70%),
      repeating-linear-gradient(180deg, rgba(255,255,255,0.03) 0 2px, rgba(0,0,0,0.05) 2px 5px),
      linear-gradient(180deg, var(--teal-mid), var(--teal-deep) 85%);
    text-align: center;
    font-family: "Roboto Condensed", Arial, sans-serif;
  }
  .brand-name {
    position: absolute;
    top: 300px;
    left: 0;
    right: 0;
    margin: 0;
    font-family: "Oswald", "Arial Narrow", sans-serif;
    font-weight: 400;
    font-size: 104px;
    line-height: 1;
    letter-spacing: 2px;
    color: var(--aqua);
  }
  .variant {
    position: absolute;
    top: 438px;
    left: 50%;
    transform: translateX(-50%);
    width: 220px;
    height: 36px;
    line-height: 36px;
    background: var(--aqua-band);
    color: var(--white);
    font-size: 26px;
    letter-spacing: 1px;
  }
  .product-type {
    position: absolute;
    top: 510px;
    left: 0;
    right: 0;
    margin: 0;
    color: var(--white);
    font-size: 29px;
    letter-spacing: 1px;
  }
  .product-facts {
    position: absolute;
    top: 551px;
    left: 0;
    right: 0;
    margin: 0;
    color: var(--aqua-band);
    font-size: 12.5px;
    letter-spacing: 0.4px;
    filter: brightness(1.3);
  }
</style>
</head>
<body>
  <div class="label">
    <div class="label-panel">
      <h1 class="brand-name">Q-VIBE</h1>
      <div class="variant">PELLET</div>
      <p class="product-type">ENERGY TABLET</p>
      <p class="product-facts">DIETARY SUPPLEMENT • 120 CAPSULES VEGETARIAN</p>
    </div>
  </div>
</body>
</html>
```